Design Startseite Kanzlei-Homepage
Zielgruppe
Wir sind eine Rechtsanwaltskanzlei in Talheim (Allgäu) und regional sowie überregional in verschiedenen Rechtsgebieten tätig. Unsere Zielgruppe sind sowohl private als auch gewerbliche Mandanten.
Aufgabenstellung
Die bestehende Gestaltung wirkt derzeit aus unserer Sicht überholt. Insbesondere soll das bislang dominierende Rot vollständig entfallen.
Stattdessen stellen wir uns ein modernes, hochwertiges Erscheinungsbild vor, primär in dunklen Farbtönen (Anthrazit/Schwarz) kombiniert mit Beige- bzw. warmen Naturtönen. Ziel ist eine klare visuelle Anlehnung an unsere Kanzleiräumlichkeiten (siehe Fotos).
Die Webseite soll insgesamt moderner, klarer und visuell anspruchsvoller wirken, ohne an Seriosität und Zugänglichkeit einzubüßen. Die Balance zwischen hochwertigem Erscheinungsbild und mandantenorientierter Nutzerführung steht für uns im Vordergrund.

```html
<!DOCTYPE html>
<html lang="de">
<head>
<meta charset="utf-8">
<title>Kanzlei am Lindenplatz – Startseite</title>
<link href="https://fonts.googleapis.com/css2?family=Playfair+Display:wght@400;500&family=Roboto:wght@400;500&display=swap" rel="stylesheet">
<style>
:root{
  --navy:#2b394d;
  --navy-deep:#1f2a3a;
  --light:#f2f2f2;
  --white:#ffffff;
  --text:#5b5f66;
  --heading:#6a6d72;
  --label:#4a4f58;
  --warm:#b08a62;
}
*{box-sizing:border-box;margin:0;padding:0}
html,body{width:1200px;height:3792px;overflow:hidden}
body{position:relative;font-family:"Roboto",Arial,sans-serif;color:var(--text);background:var(--white)}
.abs{position:absolute}
.serif{font-family:"Playfair Display",Georgia,serif}

/* hero */
.hero{left:0;top:0;width:1200px;height:583px;background:linear-gradient(180deg,#3d5067 0%,#55637a 30%,#6b5a4e 62%,#2f2a2a 100%)}
.brand{font-family:"Roboto",Arial,sans-serif;font-weight:500;color:var(--white);letter-spacing:1px}
.hero .brand{left:162px;top:22px;font-size:23px}
.nav{top:28px;left:586px;display:flex;gap:27px;font-size:15px;font-weight:500;color:var(--white);letter-spacing:.3px}
.nav-contact{left:939px;top:21px;width:100px;height:31px;border:2px solid var(--white);color:var(--white);font-size:14px;font-weight:500;display:flex;align-items:center;justify-content:center}
.hero-title{left:163px;top:170px;font-size:50px;line-height:56px;color:var(--white);font-weight:400}
.hero-btn{left:163px;top:312px;width:173px;height:37px;background:var(--white);color:#333;font-size:14px;display:flex;align-items:center;justify-content:center}

/* labels */
.label{font-size:13px;font-weight:500;color:var(--label);letter-spacing:.3px;display:flex;align-items:center;gap:16px}
.label::after{content:"";width:28px;height:2px;background:var(--navy)}
.btn-dark{background:var(--navy);color:var(--white);font-size:14px;font-weight:500;display:flex;align-items:center;justify-content:center}

/* intro */
.intro-left{left:0;top:583px;width:600px;height:552px;background:var(--light)}
.intro-copy{font-size:15px;line-height:22px;color:var(--text)}

/* gallery */
.gallery{left:0;top:1135px;width:1200px;height:633px;background:var(--navy)}
.photo{position:absolute}
.dot{width:18px;height:18px;border-radius:50%;border:1.5px solid var(--white);top:1666px}
.dot.active{background:var(--white)}

/* team */
.section-heading{font-family:"Playfair Display",Georgia,serif;font-size:27px;color:var(--heading);font-weight:400}

/* reviews */
.reviews{left:0;top:2263px;width:1200px;height:454px;background:var(--light)}
.review-title{left:0;top:2340px;width:1200px;display:flex;justify-content:center;align-items:center;gap:16px;font-size:13px;font-weight:500;color:var(--label)}
.review-title span.line{width:28px;height:2px;background:var(--navy)}
.quote{width:210px;font-size:15px;line-height:22px;top:2437px}
.person{width:206px;text-align:right;font-size:15px;top:2608px;letter-spacing:.3px}

/* footer */
.footer{left:0;top:3184px;width:1200px;height:608px;background:var(--navy)}
.footer .brand{left:162px;top:3272px;font-size:33px}
.info{left:163px;color:var(--white);font-size:12px;line-height:15px;display:flex;gap:6px}
.info svg{flex:none;margin-top:1px}
.field{left:640px;width:399px;border:1.5px solid #c9ced6;color:var(--white);font-size:14px;padding:0 26px;display:flex;align-items:center}
.checkbox{left:640px;top:3541px;width:24px;height:23px;background:var(--white)}
.consent{left:690px;top:3543px;width:330px;font-size:9px;line-height:12px;color:var(--white)}
.send{left:640px;top:3600px;width:399px;height:36px;background:var(--white);color:#222;font-size:14px;font-weight:500;display:flex;align-items:center;justify-content:center}
.legal{left:0;top:3752px;width:1200px;text-align:center;font-size:10px;color:var(--white);font-weight:500}
</style>
</head>
<body>

<!-- Hero -->
<div class="abs hero" role="img" aria-label="Foto: Kanzleigebäude bei Abenddämmerung mit beleuchteten Fenstern und Lichtspuren auf der Straße"></div>
<div class="abs brand" style="left:162px;top:22px;font-size:22px">KANZLEI AM LINDENPLATZ</div>
<nav class="abs nav"><span>ÜBER UNS</span><span>UNSERE EXPERTISE</span><span>KARRIERE</span></nav>
<div class="abs nav-contact">KONTAKT</div>
<h1 class="abs hero-title serif">Ihr gutes Recht –<br>konsequent durchgesetzt</h1>
<div class="abs hero-btn">Termin vereinbaren</div>

<!-- Intro -->
<div class="abs intro-left"></div>
<div class="abs label" style="left:163px;top:678px">ÜBER UNS</div>
<p class="abs intro-copy serif" style="left:163px;top:716px;width:250px">Die Kanzlei am Lindenplatz in Talheim ist eine auf verschiedene Rechtsgebiete spezialisierte Anwaltskanzlei und bietet umfassende rechtliche Beratung sowie Vertretung, sowohl außergerichtlich als auch vor Gericht, in nationalen Angelegenheiten. Schwerpunkte liegen unter anderem im Verkehrsrecht, Strafrecht sowie im Arbeits-, Erb-, Miet-, Bau- und Familienrecht.</p>
<div class="abs btn-dark" style="left:163px;top:1039px;width:173px;height:39px">Mehr zur Kanzlei</div>

<div class="abs label" style="left:736px;top:677px">UNSERE EXPERTISE</div>
<p class="abs intro-copy" style="left:736px;top:716px;width:240px">Wir stehen Ihnen mit fundierter rechtlicher Beratung und konsequenter Vertretung in wichtigen Bereichen des Zivil- und Strafrechts zur Seite. Unser Tätigkeitsschwerpunkt umfasst insbesondere das Familienrecht, Arbeitsrecht, Verkehrsrecht und Strafrecht sowie das Erbrecht und das Mietrecht bzw. Wohnungseigentumsrecht.</p>
<div class="abs btn-dark" style="left:736px;top:1039px;width:193px;height:39px">Alle Schwerpunkte</div>

<!-- Gallery -->
<div class="abs gallery"></div>
<div class="photo" style="left:0;top:1269px;width:389px;height:355px;background:linear-gradient(160deg,#e8e4dc,#9b8a72 55%,#2d2b28)" role="img" aria-label="Foto: Wartebereich mit dunklen Sitzbänken und Bergpanorama-Wandbild"></div>
<div class="photo" style="left:415px;top:1269px;width:483px;height:355px;background:linear-gradient(180deg,#a9a9a6,#8c8b88 45%,#5c5d60)" role="img" aria-label="Foto: Gruppenbild des Kanzleiteams auf gepflastertem Platz"></div>
<div class="photo" style="left:927px;top:1269px;width:273px;height:355px;background:linear-gradient(90deg,#c79b5e,#efece6 40%,#4b4c4e)" role="img" aria-label="Foto: Flur der Kanzlei mit Holzverkleidung"></div>
<div class="abs dot" style="left:556px"></div>
<div class="abs dot" style="left:580px"></div>
<div class="abs dot active" style="left:605px"></div>
<div class="abs dot" style="left:630px"></div>

<!-- Team -->
<div class="abs label" style="left:162px;top:1841px">TEAM</div>
<h2 class="abs section-heading" style="left:162px;top:1877px">Unsere Experten</h2>
<p class="abs intro-copy" style="left:162px;top:1943px;width:335px">Wir vereinen hochqualifizierte Rechtsanwältinnen und Rechtsanwälte mit umfassender Expertise in allen wesentlichen Bereichen wirtschaftlicher Tätigkeit. Die Kanzlei berät und vertritt ihre Mandanten sowohl außergerichtlich als auch in gerichtlichen und schiedsgerichtlichen Verfahren und ist dabei in nationalen wie auch grenzüberschreitenden Angelegenheiten tätig.</p>
<div class="abs btn-dark" style="left:162px;top:2155px;width:171px;height:37px">Unsere Teams</div>
<div class="photo" style="left:576px;top:1838px;width:397px;height:267px;background:linear-gradient(135deg,#d7d2ca,#b39470 60%,#efeae2)" role="img" aria-label="Foto: Besprechungsraum mit Holzelementen"></div>
<div class="photo" style="left:642px;top:1862px;width:397px;height:266px;background:linear-gradient(160deg,#eef0ee,#c8cbc6 45%,#2e3438)" role="img" aria-label="Foto: Drei Anwälte im Gespräch am Besprechungstisch"></div>

<!-- Reviews -->
<div class="abs reviews"></div>
<div class="abs review-title"><span class="line"></span>MANDANTENBEWERTUNGEN<span class="line"></span></div>
<p class="abs quote" style="left:210px">„Engagiertes Team mit klarer Kommunikation und hoher Fachkenntnis. Besonders die schnelle Reaktionszeit und die transparente Vorgehensweise haben mich überzeugt.“</p>
<p class="abs quote" style="left:498px">„Sehr kompetente und verständliche Beratung. Ich habe mich jederzeit gut aufgehoben gefühlt und mein Anliegen wurde schnell und zuverlässig bearbeitet</p>
<p class="abs quote" style="left:785px">„Professionell, freundlich und lösungsorientiert. Meine Erwartungen wurden nicht nur erfüllt, sondern deutlich übertroffen.“</p>
<div class="abs person" style="left:210px">PERSON XY</div>
<div class="abs person" style="left:498px">PERSON XY</div>
<div class="abs person" style="left:785px">PERSON XY</div>

<!-- Image video -->
<div class="abs label" style="left:162px;top:2809px">IMAGEVIDEO</div>
<h2 class="abs section-heading" style="left:162px;top:2845px">Lernen Sie uns kennen!</h2>
<p class="abs intro-copy" style="left:162px;top:2912px;width:335px">Lernen Sie uns und unsere Kanzlei in einem kurzen Imagefilm näher kennen. Erhalten Sie einen Einblick in unsere Arbeitsweise, unser Team und unsere Schwerpunkte. So bekommen Sie einen ersten Eindruck davon, wie wir Sie in Ihren rechtlichen Anliegen unterstützen können.</p>
<div class="photo" style="left:573px;top:2785px;width:466px;height:314px;background:linear-gradient(90deg,#6e4a2c,#b9b6ae 45%,#e7e3dc 70%,#7a5030);" role="img" aria-label="Videovorschau: Empfangsbereich der Kanzlei mit Holzwänden"></div>
<svg class="abs" style="left:766px;top:2900px" width="82" height="82" viewBox="0 0 82 82" aria-hidden="true">
  <circle cx="41" cy="41" r="39" fill="none" stroke="#fff" stroke-width="2.5"/>
  <path d="M33 27 L57 41 L33 55 Z" fill="none" stroke="#fff" stroke-width="2.5" stroke-linejoin="round"/>
</svg>

<!-- Footer -->
<div class="abs footer"></div>
<div class="abs brand" style="left:162px;top:3272px;font-size:31px">KANZLEI AM LINDENPLATZ</div>
<div class="abs info" style="top:3343px">
  <svg width="13" height="13" viewBox="0 0 13 13"><circle cx="6.5" cy="6.5" r="5.5" fill="none" stroke="#fff"/><path d="M6.5 3.5V6.5L8.5 8" fill="none" stroke="#fff"/></svg>
  <span>Mo – Fr 9 – 17 Uhr<br>Sa – So nach Absprache</span>
</div>
<div class="abs info" style="top:3382px">
  <svg width="13" height="13" viewBox="0 0 13 13"><path d="M6.5 12C6.5 12 2.5 7.5 2.5 5a4 4 0 0 1 8 0c0 2.5-4 7-4 7z" fill="none" stroke="#fff"/><circle cx="6.5" cy="5" r="1.4" fill="none" stroke="#fff"/></svg>
  <span>Kanzlei am Lindenplatz<br>Ahornweg 14 | 87400 Talheim</span>
</div>
<div class="abs info" style="top:3419px">
  <svg width="13" height="13" viewBox="0 0 13 13"><path d="M3 1.5l2 2.5-1.2 1.5c.8 1.6 2 2.8 3.7 3.7L9 8l2.5 2-1 1.5C6 11.5 1.5 7 1.5 2.5z" fill="none" stroke="#fff"/></svg>
  <span>0123 - 456 789 00</span>
</div>
<div class="abs info" style="top:3441px">
  <svg width="13" height="13" viewBox="0 0 13 13"><rect x="1.5" y="3" width="10" height="7.5" fill="none" stroke="#fff"/><path d="M1.5 3l5 4 5-4" fill="none" stroke="#fff"/></svg>
  <span>info@kanzlei-lindenplatz.de</span>
</div>
<div class="abs" style="left:163px;top:3502px;width:307px;height:135px;background:linear-gradient(135deg,#e9e9e9,#d4d4d4)" role="img" aria-label="Kartenausschnitt mit Standort der Kanzlei"></div>

<div class="abs field" style="top:3277px;height:35px">Name</div>
<div class="abs field" style="top:3324px;height:35px">E-Mail</div>
<div class="abs field" style="top:3372px;height:36px">Mobil</div>
<div class="abs field" style="top:3421px;height:100px;align-items:flex-start;padding-top:14px">Nachricht</div>
<div class="abs checkbox"></div>
<p class="abs consent">Ja, ich bin damit einverstanden, dass die von mir angegebenen Daten zu einer Kontaktaufnahme genutzt werden.</p>
<div class="abs send">Senden</div>

<div class="abs" style="left:586px;top:3735px;width:28px;height:2px;background:#fff"></div>
<div class="abs legal">Impressum &nbsp;|&nbsp; Datenschutz &nbsp;|&nbsp; Cookie-Management</div>

</body>
</html>
```